Coastline Premier Retreats Business Card Design

Design a business card for Coastline Premier Retreats. Look at the website for colors and reference. Card should have logo, name, title, office number, mobile number, email, URL and a tagline like, "Luxury Hotel & Resort Email Marketing" (This might change).

https://www.coastlinepremierretreats.example

The rest I will leave up to your imagination.

Contact Information for Business Card

Logo, name, title, office number, mobile number, email, URL and a tagline like, "Luxury Hotel & Resort Email Marketing" (This might change).

```html
<!DOCTYPE html>
<html lang="en">
<head>
<meta charset="utf-8">
<title>Coastline Premier Retreats – Business Card</title>
<link href="https://fonts.googleapis.com/css2?family=Michroma&family=Play:wght@400;700&display=swap" rel="stylesheet">
<style>
  :root {
    --bg: #2b2b2b;
    --card-light: #ffffff;
    --card-dark: #000000;
    --ink: #111111;
    --accent: #f07a0e;
    --paper-text: #ffffff;
  }
  * { box-sizing: border-box; margin: 0; padding: 0; }
  html, body { width: 1093px; height: 1200px; overflow: hidden; }
  body { background: var(--bg); font-family: "Play", sans-serif; position: relative; }

  .card {
    position: absolute;
    left: 265px;
    width: 578px;
    height: 356px;
    border-radius: 28px;
    box-shadow: 0 4px 10px rgba(0,0,0,.45);
  }
  .card--front { top: 226px; background: var(--card-light); color: var(--ink); }
  .card--back  { top: 621px; background: var(--card-dark); color: var(--paper-text); }

  .brand { display: flex; align-items: center; gap: 10px; font-family: "Michroma", sans-serif; }
  .brand__square { width: 14px; height: 14px; background: var(--accent); flex: none; }
  .brand__name { line-height: 1.15; }
  .brand__main { display: block; }
  .brand__sub { display: block; letter-spacing: .12em; }

  .card--front .brand { position: absolute; right: 30px; top: 76px; color: var(--ink); }
  .card--front .brand__main { font-size: 27px; }
  .card--front .brand__sub { font-size: 11.5px; }

  .holder { position: absolute; left: 31px; top: 205px; }
  .holder__name { font-family: "Michroma", sans-serif; font-size: 17px; letter-spacing: .04em; font-weight: 400; -webkit-text-stroke: .6px var(--ink); }
  .holder__title { color: var(--accent); font-size: 16px; margin-top: 0; }

  .rule { position: absolute; left: 31px; right: 31px; top: 254px; height: 1px; background: var(--ink); }

  .contacts { position: absolute; left: 31px; right: 31px; top: 273px; display: flex; justify-content: space-between; font-size: 16px; line-height: 21px; }
  .contacts__col { list-style: none; }
  .contacts__col--right { text-align: right; }
  .contacts__item { display: flex; align-items: center; gap: 6px; }
  .contacts__col--right .contacts__item { justify-content: flex-end; }
  .contacts__icon { width: 15px; height: 15px; flex: none; }
  .contacts__hl { color: var(--accent); }

  .card--back .brand { position: absolute; left: 0; right: 0; top: 135px; justify-content: center; color: var(--paper-text); }
  .card--back .brand__main { font-size: 34px; }
  .card--back .brand__sub { font-size: 14px; }
  .tagline { position: absolute; left: 0; right: 0; top: 296px; text-align: center; color: var(--accent); font-size: 17px; letter-spacing: .03em; }
</style>
</head>
<body>
  <section class="card card--front">
    <div class="brand">
      <span class="brand__square"></span>
      <span class="brand__name"><span class="brand__main">COASTLINE</span><span class="brand__sub">PREMIER RETREATS</span></span>
    </div>

    <div class="holder">
      <h1 class="holder__name">DANIEL WHITMORE</h1>
      <p class="holder__title">Managing Director</p>
    </div>

    <div class="rule"></div>

    <div class="contacts">
      <ul class="contacts__col">
        <li class="contacts__item">
          <svg class="contacts__icon" viewBox="0 0 16 16"><path d="M3 1.5l2.5 0 1 3.5-1.6 1.2c.9 1.9 2.2 3.2 4 4l1.2-1.6 3.5 1v2.5c0 .8-.7 1.4-1.5 1.4C6.6 13.2 2.3 8.9 1.6 3 1.6 2.2 2.2 1.5 3 1.5z" fill="none" stroke="#f07a0e" stroke-width="1.6"/></svg>
          <span>044-555 010 218</span>
        </li>
        <li class="contacts__item">
          <svg class="contacts__icon" viewBox="0 0 16 16"><rect x="3.5" y="1" width="9" height="14" rx="1.5" fill="none" stroke="#f07a0e" stroke-width="1.5"/><circle cx="8" cy="12.6" r=".9" fill="#f07a0e"/></svg>
          <span>044-555 010 218</span>
        </li>
      </ul>
      <ul class="contacts__col contacts__col--right">
        <li class="contacts__item">
          <span>hello@coastlinepremier.example</span>
          <svg class="contacts__icon" viewBox="0 0 16 16"><rect x="0.5" y="3" width="15" height="10" fill="#f07a0e"/><path d="M0.5 3l7.5 6 7.5-6M0.5 13l5.5-5M15.5 13l-5.5-5" fill="none" stroke="#fff" stroke-width="1"/></svg>
        </li>
        <li class="contacts__item">
          <span>www.<span class="contacts__hl">coastlinepremierretreats</span>.example</span>
          <svg class="contacts__icon" viewBox="0 0 16 16"><g fill="none" stroke="#f07a0e" stroke-width="1.3"><circle cx="8" cy="8" r="6.8"/><ellipse cx="8" cy="8" rx="3" ry="6.8"/><path d="M1.2 8h13.6M2.3 4.5h11.4M2.3 11.5h11.4"/></g></svg>
        </li>
      </ul>
    </div>
  </section>

  <section class="card card--back">
    <div class="brand">
      <span class="brand__square"></span>
      <span class="brand__name"><span class="brand__main">COASTLINE</span><span class="brand__sub">PREMIER RETREATS</span></span>
    </div>
    <p class="tagline">Luxury Hotel &amp; Resort Email Marketing</p>
  </section>
</body>
</html>
```